Website Homepage Design

Tarvento Care Partners Inc. is a Canadian financial services company that specialize in the delivery and administration of alternative health benefit solutions. Tarvento is seeking to adjust their brand and develop a new website.

We like the design and layout of the website below but are not looking for an exact replica (be creative):

http://www.quellaroforum.example/

We want the colour scheme to be clean white and "fresh green", possibly with orange accents (links).

This posting is only for a website homepage design (no coding), but anyone who includes a new logo, in addition to the design, will get priority.

Best of luck,

Orrin
Updates

Project is guaranteed.

Please let me know if you are currently working on a design.

Thank you,

Orrin

*Update:

Two example websites with good colour scheme/design:

- http://blimeden.example/
- http://www.faltrukidscove.example.au/

I have attached a wireframe and colour scheme to the project brief. The main colour should be the green one. Other colours can be used for highlights and accents, etc.

Target Market(s)

Business owners age 50+

Industry/Entity Type

Financial

Requirements
Must have
• - Clear and simple design
- Area for video (similar to http://www.quellaroforum.example)
Should not have
• - Lots of pictures

```html
<!DOCTYPE html>
<html lang="en">
<head>
<meta charset="utf-8">
<title>Tarvento Care Partners – Home</title>
<link href="https://fonts.googleapis.com/css2?family=Anton&family=EB+Garamond:ital,wght@0,400;1,400&family=Open+Sans:wght@400;600&display=swap" rel="stylesheet">
<style>
:root{
  --orange:#f47c0a;
  --green:#5aa97c;
  --green-dark:#3f8a60;
  --green-bright:#6bbf3a;
  --ink:#58574f;
  --text:#555;
  --muted:#777;
  --line:#e4e7e5;
  --band:#f4f7f5;
  --teal:#4f9d8a;
}
*{margin:0;padding:0;box-sizing:border-box}
html,body{width:1200px;height:1019px;overflow:hidden;background:#fff}
body{position:relative;font-family:"Open Sans",Arial,sans-serif;color:var(--text)}
.abs{position:absolute}
.top-rule{left:0;top:0;width:1200px;height:3px;background:var(--orange)}
.brand{left:144px;top:36px;display:flex;align-items:center;gap:8px}
.brand-name{font-size:40px;font-weight:400;color:var(--orange);letter-spacing:-1px;line-height:1}
.brand-dot{width:12px;height:12px;border-radius:50%;background:var(--green-bright)}
.tagline{left:305px;top:67px;font-family:"EB Garamond",serif;font-size:14px;color:#888}
.tagline .easy{color:var(--teal)}
.tagline .afford{color:var(--green)}
.login{left:964px;top:14px;width:100px;height:35px;border-radius:3px;background:linear-gradient(#6cbc8d,#48966b);border:1px solid #3d845d;color:#fff;font-size:13px;font-weight:600;text-align:center;line-height:33px}
.nav{right:136px;top:69px;display:flex;font-family:"EB Garamond",serif;font-size:15px;color:#777}
.nav span{padding:0 7px;border-left:1px solid #ddd}
.nav span:first-child{border-left:none}
.nav span:last-child{padding-right:0}
.divider{height:1px;background:linear-gradient(90deg,transparent,var(--line) 15%,var(--line) 85%,transparent)}
.video{left:205px;top:145px;width:460px;height:310px;border-radius:14px 14px 0 0;background:linear-gradient(160deg,#e9e9ea,#b9b9bb 55%,#d7d7d8)}
.video svg{position:absolute;left:178px;top:106px}
.video-base{left:124px;top:453px;width:616px;height:16px;border-radius:0 0 40px 40px;background:linear-gradient(#e2e2e3,#b4b4b6)}
.headline{left:716px;top:138px;font-family:"Anton",sans-serif;font-size:36px;color:var(--ink);line-height:1.1;letter-spacing:1.6px}
.cost{left:716px;top:184px;font-family:"Anton",sans-serif;font-size:76px;line-height:1;color:var(--ink);letter-spacing:3px}
.cost b{font-weight:400;color:var(--orange)}
.hero-image{left:966px;top:180px;width:74px;height:88px;border-radius:6px;background:linear-gradient(#9fd45e,#e8f1e2)}
.intro{left:720px;top:272px;width:330px;font-size:13.5px;line-height:18px;letter-spacing:.4px;color:#555}
.cta{left:719px;top:354px;width:198px;height:53px;border-radius:4px;background:linear-gradient(#6ec292,#4a9b6e);border:1px solid #3f8a60;color:#fff;font-size:21px;text-align:center;line-height:51px;letter-spacing:.5px}
.call{left:742px;top:417px;font-size:14px;color:#111;letter-spacing:.6px}
.card{top:545px;height:95px;background:linear-gradient(90deg,rgba(240,245,242,0),#f3f7f5 20%,#f3f7f5 80%,rgba(240,245,242,0));border-bottom:2px solid #eef1ef}
.card .why{position:absolute;top:14px;font-family:"EB Garamond",serif;font-size:17px;color:var(--orange)}
.card .title{position:absolute;top:22px;font-family:"EB Garamond",serif;font-size:34px;color:var(--ink)}
.card .more{position:absolute;top:62px;font-size:14px;color:#666;letter-spacing:.4px;display:flex;align-items:center;gap:6px}
.bulb{width:9px;height:9px;border-radius:50%;background:var(--green-bright);box-shadow:0 6px 0 -3px #7a8a70}
.quote{left:160px;top:716px}
.quote-text{left:185px;top:750px;width:300px;font-family:"EB Garamond",serif;font-style:italic;font-size:28px;line-height:30px;color:#666}
.quote-mark{left:176px;top:734px;font-family:"EB Garamond",serif;font-size:80px;color:#aaa;line-height:1}
.quote-by{left:383px;top:913px;font-size:13px;font-weight:600;color:#666}
.col h3{font-size:17px;font-weight:400;color:#777;letter-spacing:.3px;line-height:22px}
.col li{list-style:none;font-size:12.5px;line-height:20px;color:#777;letter-spacing:.3px}
.col li.help{color:#1d8a4a}
.badges{left:760px;top:888px;display:flex;gap:8px;align-items:center}
.badge{background:#cfd2d0;border-radius:4px}
.footer{left:0;top:958px;width:1200px;height:61px;background:var(--band)}
.copy{left:131px;top:980px;font-size:11.5px;color:#777;letter-spacing:.3px}
.follow{left:916px;top:980px;font-size:12px;color:#777;display:flex;align-items:center;gap:4px}
.follow i{display:inline-block;width:16px;height:16px;border-radius:2px;background:#4a78b6}
</style>
</head>
<body>
<div class="abs top-rule"></div>

<header>
  <div class="abs brand"><span class="brand-name">Tarvento</span><span class="brand-dot"></span></div>
  <div class="abs tagline">We make it <span class="easy">easy.</span> We make it <span class="afford">affordable.</span></div>
  <div class="abs login">Login | Join</div>
  <nav class="abs nav"><span>Small Business</span><span>Big Business</span><span>Broker Business</span><span>Our Company</span><span>Contact Us</span></nav>
</header>
<div class="abs divider" style="left:260px;top:105px;width:720px"></div>

<section class="hero">
  <div class="abs video" role="img" aria-label="Introductory video">
    <svg width="110" height="110" viewBox="0 0 110 110"><circle cx="55" cy="55" r="53" fill="rgba(255,255,255,.35)"/><path d="M40 30 L82 55 L40 80Z" fill="#fff"/></svg>
  </div>
  <div class="abs video-base"></div>
  <div class="abs headline">Cut your healthcare</div>
  <div class="abs cost"><b>CO$T</b> in</div>
  <div class="abs hero-image" role="img" aria-label="Photo of a sliced green apple"></div>
  <p class="abs intro">We put control back in your hands by helping<br>you reign in costs and maximize benefits.<br>On average, you could save 20-30% over<br>traditional group plans.</p>
  <div class="abs cta">Lest Get Started!</div>
  <div class="abs call">Call: 1-800-Tar-Vent</div>
</section>
<div class="abs divider" style="left:240px;top:500px;width:740px"></div>

<section class="cards">
  <div class="abs card" style="left:152px;width:282px"><span class="why" style="left:57px">why</span><span class="title" style="left:76px">smallbiz?</span><span class="more" style="left:125px">Learn More <span class="bulb"></span></span></div>
  <div class="abs card" style="left:460px;width:285px"><span class="why" style="left:65px">why</span><span class="title" style="left:93px">bigbiz?</span><span class="more" style="left:136px">Learn More <span class="bulb"></span></span></div>
  <div class="abs card" style="left:768px;width:282px"><span class="why" style="left:42px">why</span><span class="title" style="left:70px">brokerbiz?</span><span class="more" style="left:142px">Learn More <span class="bulb"></span></span></div>
</section>
<div class="abs divider" style="left:380px;top:683px;width:500px"></div>

<section class="testimonial">
  <svg class="abs quote" width="345" height="200" viewBox="0 0 345 200"><path d="M40 3 H338 V115 Q338 150 295 152 H260 Q248 165 230 190 L240 152 H14 Q3 152 3 140 V40 Q3 3 40 3Z" fill="#f8faf9" stroke="#c9ccca" stroke-width="1.5"/></svg>
  <div class="abs quote-mark">“</div>
  <p class="abs quote-text">&nbsp;&nbsp;&nbsp;&nbsp;&nbsp;Truely amazing. This is exactly what each financial services should be offering.</p>
  <div class="abs quote-by">– Guest Customer</div>
</section>

<section class="links">
  <div class="abs col" style="left:568px;top:737px"><h3>Menu</h3><ul><li>Small Business</li><li>Big Business</li><li>Broker Business</li><li>Our Company</li><li>Contact Us</li></ul></div>
  <div class="abs col" style="left:721px;top:737px"><h3>Who We Are</h3><ul><li>About Us</li><li>Meet the Team</li><li>News</li><li>Careers</li></ul></div>
  <div class="abs col" style="left:878px;top:737px"><h3>Customer Service</h3><ul><li class="help">Click for Live Help!</li><li>Call us at 1-1800-Tar-Vent</li><li>Email: info@tarvento.example</li></ul></div>
  <div class="abs badges">
    <span class="badge" style="width:114px;height:32px"></span>
    <span class="badge" style="width:42px;height:34px;border-radius:50%"></span>
    <span class="badge" style="width:24px;height:36px"></span>
    <span class="badge" style="width:70px;height:32px;border-radius:16px"></span>
  </div>
</section>

<footer class="abs footer"></footer>
<div class="abs copy">Copyright © 2010 Brennick Advisory Group Inc. Ver. 1.0.298</div>
<div class="abs follow">Follow us&nbsp;&nbsp;<i></i><i style="background:#5ab4d8"></i><i style="background:#c9302c"></i></div>
</body>
</html>
```